4th Generation Family Business Needs a New Card Design!

We are a family owned 4th Generation company. We are based in the Sydney, Australia area and we are desperately in need of a more modern and classy card. We are monumental masons who design, supply & erect lasting memorials throughout cemeteries in Sydney. Our customers are normally in a period of grieving. I have attached logo files that will need to be implemented on the card. Company was established 1935. Australian Owned and Operated. Card needs to be designed to PIXO.com specification.

Target Market(s)

Our target market is based upon people that a grieving for family members that have passed away. We also deal with alot of companies that own and operate cemeteries.

Industry/Entity Type

Business

Contact Information for Business Card

Simon Harcourt, Operations Manager, 0417293086, simon@harcourtmemorials.com.au
Lewis Harcourt, Director, 0491630572, lewis@harcourtmemorials.com.au
Phone # 02 9561 3048
Website: www.harcourtmemorials.com.au
Address: Suite 17, 8 Palfrey Lane, West Carlow, Sydney NSW 2156

Font styles to use
Serif
Decorative
Script

Requirements
Must have
• Would like to see the logo nicely implemented with a modern design. Embossed lettering would be a nice additive.

```html
<!DOCTYPE html>
<html lang="en">
<head>
<meta charset="utf-8">
<title>Harcourt Memorials – Business Cards</title>
<link rel="stylesheet" href="https://fonts.googleapis.com/css2?family=Open+Sans:ital,wght@0,400;0,700;1,400&display=swap">
<style>
  :root {
    --backdrop: #5b5c5f;
    --card: #fffdfb;
    --card-warm: #fbefe8;
    --ink: #1c1c1c;
    --ink-soft: #2a2a2a;
    --gilt: #c99a2e;
  }
  * { box-sizing: border-box; margin: 0; padding: 0; }
  html, body {
    width: 1200px; height: 675px; overflow: hidden;
    background: var(--backdrop);
    font-family: "Open Sans", Arial, sans-serif;
    color: var(--ink);
  }
  .sheet {
    width: 1200px; height: 675px;
    display: flex; justify-content: center; align-items: center; gap: 40px;
  }
  .card {
    width: 520px; height: 317px;
    background: linear-gradient(110deg, var(--card-warm) 0%, var(--card) 45%, var(--card) 100%);
    border: 3px solid var(--gilt);
    position: relative;
    display: flex; align-items: center;
  }
  .brand {
    display: flex; align-items: center; gap: 12px;
  }
  .brand-mark {
    width: 30px; height: 30px;
    background: var(--ink);
    flex: none;
  }
  .brand-name {
    font-weight: 400;
    font-size: 22px;
    line-height: 1.1;
    letter-spacing: 0.06em;
    text-transform: uppercase;
    color: var(--ink);
  }
  .card-front { padding: 0 26px 0 40px; justify-content: space-between; }
  .card-front .brand { width: 200px; }
  .contact { width: 230px; font-size: 11.5px; line-height: 1.45; color: var(--ink-soft); }
  .contact-name { font-weight: 700; font-size: 15px; letter-spacing: 0.05em; text-transform: uppercase; color: var(--ink); }
  .contact-role { font-style: italic; margin-bottom: 8px; }
  .contact-address { margin-bottom: 8px; }
  .contact-lines { list-style: none; }
  .card-back { justify-content: center; }
  .card-back .brand-name { font-size: 26px; }
  .card-back .brand-mark { width: 36px; height: 36px; }
</style>
</head>
<body>
  <main class="sheet">
    <section class="card card-front" aria-label="Card front">
      <div class="brand">
        <span class="brand-mark" aria-hidden="true"></span>
        <span class="brand-name">Harcourt<br>Memorials</span>
      </div>
      <div class="contact">
        <p class="contact-name">Simon Harcourt</p>
        <p class="contact-role">Operations Manager</p>
        <p class="contact-address">Suite 17, 8 Palfrey Lane<br>West Carlow, Sydney NSW 2156</p>
        <ul class="contact-lines">
          <li>Mobile : 0417293086</li>
          <li>Phone : 02 9561 3048</li>
          <li>simon@harcourtmemorials.com.au</li>
          <li>www.harcourtmemorials.com.au</li>
        </ul>
      </div>
    </section>
    <section class="card card-back" aria-label="Card back">
      <div class="brand">
        <span class="brand-mark" aria-hidden="true"></span>
        <span class="brand-name">Harcourt<br>Memorials</span>
      </div>
    </section>
  </main>
</body>
</html>
```